Tidewell Homecare

I am looking to have a website designed for a housekeeping company that looks similar to this one. https://marloweshomecare.example/

I need 5 websites designed but will start with this one to see how I like it.

Industry/Entity Type

House Cleaning

Coding

Coded - Design and coding required

Number of Pages Required

5+ page

Font styles to use
Serif
Script

Colors
ffffff
fdf9cf
fbf289
fbee3f
d6edf3
86cae7
33a6d7
edf1f8
cedeed

```html
<!DOCTYPE html>
<html lang="en">
<head>
<meta charset="utf-8">
<title>Tidewell Homecare</title>
<link href="https://fonts.googleapis.com/css2?family=Montserrat:wght@400;500;600;700;800&family=Quicksand:wght@400;500;600;700&display=swap" rel="stylesheet">
<style>
:root{
  --blue:#33a6d7;
  --blue-deep:#1d8fd0;
  --blue-soft:#86cae7;
  --blue-pale:#d6edf3;
  --yellow:#fbee3f;
  --yellow-soft:#fbf289;
  --cream:#fdf9cf;
  --grey:#edf1f8;
  --grey-band:#ececec;
  --ink:#222831;
  --text:#5b6168;
  --white:#ffffff;
  --black:#0a0a0a;
}
*{margin:0;padding:0;box-sizing:border-box}
html,body{width:1200px;height:4422px;overflow:hidden}
body{position:relative;background:var(--white);font-family:'Quicksand',sans-serif;color:var(--text)}
.abs{position:absolute}
a{color:inherit;text-decoration:none}

/* top bar */
.topbar{left:0;top:0;width:1200px;height:38px;background:var(--blue-deep);color:var(--white);font:500 14px 'Montserrat',sans-serif;display:flex;align-items:center;justify-content:space-between;padding:0 88px}
.topbar span{display:flex;align-items:center;gap:8px}
.header{left:0;top:38px;width:1200px;height:74px;background:var(--white)}
.brand{left:88px;top:56px;font:500 27px 'Quicksand',sans-serif;color:var(--blue)}
.call{right:108px;top:58px;display:flex;align-items:center;gap:12px;font:600 19px 'Montserrat',sans-serif;color:var(--blue-deep)}
.call .dot{width:38px;height:38px;border-radius:50%;background:var(--yellow);display:flex;align-items:center;justify-content:center}
.call b{font-weight:700}

/* hero */
.hero{left:0;top:112px;width:1200px;height:560px;background:linear-gradient(100deg,#d9e7ef 0%,#5aa7d0 35%,#3f7da6 60%,#6b8aa3 100%)}
.nav{left:0;top:112px;width:1200px;height:53px;background:rgba(255,255,255,.78);display:flex;align-items:center;padding-left:160px}
.nav a{font:500 16px 'Montserrat',sans-serif;color:var(--ink);padding:0 28px;border-right:1px solid rgba(0,0,0,.08);line-height:53px}
.nav a.active{color:var(--blue)}
.hero-title{left:668px;top:258px;color:var(--white);line-height:1.0}
.hero-title .b{font:800 64px 'Montserrat',sans-serif;display:block}
.hero-title .l{font:400 64px 'Montserrat',sans-serif;display:block}
.hero-sub{left:668px;top:410px;font:400 20px 'Montserrat',sans-serif;color:var(--white)}
.btn-est{left:666px;top:466px;width:184px;height:48px;border-radius:24px;background:var(--blue-deep);color:var(--white);font:700 15px 'Montserrat',sans-serif;display:flex;align-items:center;justify-content:center}
.arrow-c{width:36px;height:36px;border:2px solid var(--white);border-radius:50%;display:flex;align-items:center;justify-content:center}

/* about */
.eyebrow{font:500 13px 'Montserrat',sans-serif;letter-spacing:1.5px;color:var(--ink)}
.h2{font:700 36px 'Montserrat',sans-serif;color:var(--blue-deep)}
.about-copy{left:161px;top:870px;width:406px;font:400 15px/31px 'Montserrat',sans-serif;text-align:justify;color:var(--text)}
.btn-line{height:46px;border-radius:23px;border:2px solid var(--blue-soft);border-bottom-color:var(--yellow);border-right-color:var(--yellow);font:500 17px 'Montserrat',sans-serif;color:var(--blue);display:flex;align-items:center;justify-content:center}
.about-photo{left:610px;top:810px;width:430px;height:375px;border-radius:60px 20px 60px 60px;background:linear-gradient(135deg,#e9f1ea 0%,#cfe3d6 40%,#f2b233 55%,#8aa8c7 100%);box-shadow:0 10px 30px rgba(0,0,0,.12)}

/* benefits */
.benefits{left:0;top:1283px;width:1200px;height:812px;background:linear-gradient(180deg,#3d9ad8,#3a9ad9 60%,#4aa3dc)}
.benefits-title{left:0;top:1400px;width:1200px;text-align:center;color:var(--white)}
.benefits-title .e{font:500 13px 'Montserrat',sans-serif;letter-spacing:2px;display:block;margin-bottom:6px}
.benefits-title .t{font:400 36px 'Montserrat',sans-serif}
.benefits-title .t b{font-weight:700}
.ring{width:236px;height:236px;border-radius:50%;border:8px solid var(--white);color:var(--white);text-align:center;display:flex;flex-direction:column;align-items:center;justify-content:center;padding:0 4px}
.ring h3{font:500 19px 'Montserrat',sans-serif;margin:8px 0 6px;white-space:nowrap}
.ring p{font:400 13px/22px 'Montserrat',sans-serif;width:170px}
.bubble{border-radius:50%;background:var(--white)}

/* services */
.svc-head{left:0;top:2196px;width:1200px;text-align:center}
.tile{width:151px;height:139px;border-radius:38px 8px 38px 38px;overflow:hidden}
.tile-label{display:flex;align-items:flex-end;justify-content:center;padding-bottom:14px;color:var(--white);font:500 15px/19px 'Montserrat',sans-serif;text-align:center}
.svc-copy{left:700px;top:2306px;width:411px;font:400 15px/31px 'Montserrat',sans-serif;text-align:right;color:var(--text)}

/* blog */
.blog{left:0;top:2690px;width:1200px;height:762px;background:var(--grey-band)}
.blog-head{left:0;top:2810px;width:1200px;text-align:center}
.card{width:321px;height:441px;background:var(--white);box-shadow:0 6px 18px rgba(0,0,0,.08)}
.card .img{height:220px}
.card .date{position:absolute;left:16px;top:200px;height:38px;padding:0 20px;border-radius:19px;background:var(--blue-deep);color:var(--white);font:500 14px 'Montserrat',sans-serif;display:flex;align-items:center}
.card h4{position:absolute;left:22px;top:260px;font:500 22px 'Montserrat',sans-serif;color:var(--ink)}
.card p{position:absolute;left:22px;top:302px;width:280px;font:400 13.5px/27px 'Montserrat',sans-serif;color:#777}
.card .foot{position:absolute;left:20px;right:20px;top:384px;border-top:1px solid #eee;padding-top:16px;display:flex;justify-content:space-between;align-items:center;font:500 14px 'Montserrat',sans-serif;color:var(--blue-deep)}

/* testimonial */
.testi-photo{left:620px;top:3440px;width:580px;height:580px;background:radial-gradient(circle at 60% 45%,#cfe3ee 0%,#e9eef2 45%,#f7f8fa 75%)}
.testi-card{left:144px;top:3580px;width:414px;height:300px;border-radius:40px 40px 40px 8px;background:linear-gradient(135deg,#33a6d7 0%,#7cc69b 45%,#fbee3f 100%);color:var(--white);padding:44px 42px}
.testi-card .name{font:500 20px 'Montserrat',sans-serif;letter-spacing:1px}
.testi-card .stars{margin:10px 0 14px;display:flex;gap:8px}
.testi-card p{font:400 14px/29px 'Montserrat',sans-serif;text-align:justify}
.testi-card a{display:inline-block;margin-top:10px;font:500 14px 'Montserrat',sans-serif;text-decoration:underline}

/* footer */
.footer{left:0;top:4010px;width:1200px;height:412px;background:var(--black);color:var(--white)}
.fcol h5{font:500 18px 'Montserrat',sans-serif;margin-bottom:22px}
.fcol li{list-style:none;font:400 13px/27px 'Montserrat',sans-serif}
.fcol p{font:400 13px/29px 'Montserrat',sans-serif}
.sub{width:280px;height:40px;border-radius:20px;background:var(--white);display:flex;align-items:center;justify-content:space-between;padding:0 4px 0 16px;margin-top:14px}
.sub span{font:400 12px 'Montserrat',sans-serif;color:#888}
.sub b{height:32px;padding:0 16px;border-radius:16px;background:var(--yellow);color:var(--blue-deep);font:500 13px 'Montserrat',sans-serif;display:flex;align-items:center}
.social{display:flex;gap:22px;margin-top:30px}
.social i{width:12px;height:12px;border-radius:50%;background:var(--white);display:block}
.copy-bar{left:0;top:4378px;width:1200px;height:44px;display:flex;align-items:center;justify-content:space-between;padding:0 90px}
.copy-bar .nm{font:700 19px 'Quicksand',sans-serif;color:var(--blue)}
.copy-bar .cr{font:400 13px 'Montserrat',sans-serif;color:var(--white)}
</style>
</head>
<body>

<div class="abs topbar">
  <span><svg width="14" height="14" viewBox="0 0 14 14"><circle cx="7" cy="7" r="6" fill="none" stroke="#fff" stroke-width="1.5"/><path d="M7 3.5V7l2.5 1.5" stroke="#fff" stroke-width="1.5" fill="none"/></svg>Mon - Thur: 8:00 am - 5:00 pm &nbsp;|&nbsp; Sat - Sun: 12:00 pm - 3:00 pm</span>
  <span><svg width="15" height="14" viewBox="0 0 15 14"><path d="M1 6L14 1 10 13 7 8z" fill="none" stroke="#fff" stroke-width="1.4"/></svg>2214 Shoreline Ave, Bayport, CA 90410</span>
</div>
<div class="abs header"></div>
<div class="abs brand">Tidewell Homecare</div>
<div class="abs call">
  <span class="dot"><svg width="18" height="18" viewBox="0 0 24 24"><path d="M6.6 10.8a15 15 0 006.6 6.6l2.2-2.2a1 1 0 011-.25 11.4 11.4 0 003.6.57 1 1 0 011 1V20a1 1 0 01-1 1A17 17 0 013 4a1 1 0 011-1h3.5a1 1 0 011 1c0 1.250.2 2.450.57 3.57a1 1 0 01-.25 1z" fill="#1d8fd0"/></svg></span>
  <span>Call Us : <b>(+1 555 014 2280)</b></span>
</div>

<!-- hero -->
<div class="abs hero" role="img" aria-label="Photo of two smiling cleaners in blue uniforms wiping a table with buckets and yellow gloves"></div>
<nav class="abs nav">
  <a class="active" href="#">Home</a><a href="#">Services</a><a href="#">News</a><a href="#">Gift Card</a><a href="#">About Us</a><a href="#">Contact</a><a href="#">References</a>
</nav>
<div class="abs arrow-c" style="left:28px;top:396px"><svg width="14" height="14" viewBox="0 0 14 14"><path d="M9 2L4 7l5 5" stroke="#fff" stroke-width="2" fill="none"/></svg></div>
<div class="abs arrow-c" style="left:1138px;top:396px"><svg width="14" height="14" viewBox="0 0 14 14"><path d="M5 2l5 5-5 5" stroke="#fff" stroke-width="2" fill="none"/></svg></div>
<h1 class="abs hero-title"><span class="b">Tidewell</span><span class="l">Homecare</span></h1>
<div class="abs hero-sub">Lorem ipsum dolor sit amet, consec</div>
<a class="abs btn-est" href="#">FREE ESTIMATE</a>
<div class="abs bubble" style="left:310px;top:572px;width:50px;height:50px"></div>
<div class="abs bubble" style="left:378px;top:552px;width:16px;height:16px"></div>
<div class="abs bubble" style="left:420px;top:512px;width:14px;height:14px"></div>
<div class="abs bubble" style="left:440px;top:548px;width:9px;height:9px"></div>
<div class="abs bubble" style="left:394px;top:625px;width:48px;height:48px"></div>
<svg class="abs" style="left:0;top:600px" width="1200" height="80" viewBox="0 0 1200 80"><path d="M0 52C120 20 260 20 420 50 600 82 760 24 900 30 1040 36 1120 58 1200 44V80H0z" fill="#fff"/></svg>

<!-- about -->
<div class="abs eyebrow" style="left:161px;top:790px">ABOUT US</div>
<h2 class="abs h2" style="left:161px;top:812px">Tidewell Homecare</h2>
<p class="abs about-copy">Lorem ipsum dolor sit amet, consectetur adipiscing elit, sed do eiusmod tempor incididunt ut labore et dolore magna aliqua. Ut enim ad minim veniam, quis nostrud exercitation ullamco laboris nisi ut aliquip ex ea commodo consequat. Duis aute irure dolor in in voluptate velit esse cillum dolore eu fugiat nulla pariatur.</p>
<a class="abs btn-line" href="#" style="left:161px;top:1118px;width:152px">Read More</a>
<div class="abs about-photo" role="img" aria-label="Photo of a yellow wet floor caution sign beside a cleaner mopping a bright hall"></div>

<!-- benefits -->
<div class="abs benefits" role="img" aria-label="Blue tinted photo of a cleaner mopping an office floor behind a caution sign"></div>
<svg class="abs" style="left:0;top:1270px" width="1200" height="40" viewBox="0 0 1200 40"><path d="M0 0H1200V14C1000 30 800 10 600 18 400 26 200 6 0 14z" fill="#fff"/></svg>
<div class="abs benefits-title"><span class="e">BENEFITS</span><span class="t"><b>Why</b> Choose Us</span></div>

<div class="abs ring" style="left:188px;top:1458px">
  <svg width="44" height="44" viewBox="0 0 44 44" fill="none" stroke="#fff" stroke-width="1.8"><circle cx="22" cy="17" r="12"/><path d="M22 10l2 4.5 5 .4-3.8 3.2 1.2 4.8L22 20.3l-4.4 2.6 1.2-4.8L15 14.9l5-.4z"/><path d="M14 26l-5 12 5-2 3 4 4-9M30 26l5 12-5-2-3 4-4-9"/></svg>
  <h3>High Quality</h3><p>Lorem ipsum dolor sit amet, consectetur</p></div>
<div class="abs ring" style="left:483px;top:1458px">
  <svg width="44" height="44" viewBox="0 0 44 44" fill="none" stroke="#fff" stroke-width="1.8"><circle cx="24" cy="14" r="9"/><path d="M24 9v10M21 11.5h5a2 2 0 010 4h-4a2 2 0 000 4h5"/><path d="M4 32h8l8 3h8a3 3 0 000-6h-7M12 38l10 3 16-8a3 3 0 00-3-5l-9 4"/></svg>
  <h3>Low Cost</h3><p>Lorem ipsum dolor sit amet, consectetur</p></div>
<div class="abs ring" style="left:785px;top:1458px">
  <svg width="44" height="44" viewBox="0 0 44 44" fill="none" stroke="#fff" stroke-width="1.8"><circle cx="22" cy="28" r="11"/><path d="M22 17c-4-4-4-10 0-14 4 4 4 10 0 14z"/><path d="M17 28c3 0 5 3 5 6M27 26c-2 2-5 2-5 2"/></svg>
  <h3>Eco-Friendly</h3><p>Lorem ipsum dolor sit amet, consectetur</p></div>
<div class="abs ring" style="left:188px;top:1733px">
  <svg width="44" height="44" viewBox="0 0 44 44" fill="none" stroke="#fff" stroke-width="1.8"><path d="M28 4v18M22 22h12l3 18H19z"/><path d="M23 30v10M28 30v10M33 30v10"/><rect x="6" y="28" width="10" height="12"/><path d="M9 28v-4h4v4"/></svg>
  <h3>Professional Cleaning</h3><p>Lorem ipsum dolor sit amet, consectetur</p></div>
<div class="abs ring" style="left:483px;top:1733px">
  <svg width="44" height="44" viewBox="0 0 44 44" fill="none" stroke="#fff" stroke-width="1.8"><path d="M6 20h7v18H6zM13 22l6-2 4-10c2-3 5-1 4 2l-2 8h9a3 3 0 010 6h-1a3 3 0 010 6h-2a3 3 0 010 6H13"/><path d="M34 6l2 4M40 12l-4 2M28 4v4"/></svg>
  <h3>Excellent Result</h3><p>Lorem ipsum dolor sit amet, consectetur</p></div>
<div class="abs ring" style="left:785px;top:1733px">
  <svg width="44" height="44" viewBox="0 0 44 44" fill="none" stroke="#fff" stroke-width="1.8"><path d="M38 6c-10 0-18 6-22 16l6 6c10-4 16-12 16-22z"/><circle cx="29" cy="15" r="3"/><path d="M16 22l-7 1-4 5 8 1M22 28l-1 7-5 4-1-8M12 32l-6 6"/></svg>
  <h3>Quick Cleaning</h3><p>Lorem ipsum dolor sit amet, consectetur</p></div>

<div class="abs bubble" style="left:1124px;top:1928px;width:14px;height:14px"></div>
<div class="abs bubble" style="left:1150px;top:1962px;width:9px;height:9px"></div>
<div class="abs bubble" style="left:1086px;top:1970px;width:14px;height:14px"></div>
<div class="abs bubble" style="left:1112px;top:1988px;width:30px;height:30px"></div>
<div class="abs bubble" style="left:1016px;top:1990px;width:52px;height:52px"></div>
<div class="abs bubble" style="left:1098px;top:2040px;width:54px;height:54px"></div>
<svg class="abs" style="left:0;top:2030px" width="1200" height="70" viewBox="0 0 1200 70"><path d="M0 60C80 36 160 20 280 28 440 38 560 70 720 62 880 54 1000 34 1200 44V70H0z" fill="#fff"/></svg>

<!-- services -->
<div class="abs svc-head"><div class="eyebrow" style="margin-bottom:8px">SERVICES</div><h2 class="h2">Tidewell Homecare</h2></div>
<div class="abs tile" style="left:89px;top:2302px;background:linear-gradient(160deg,#c9c2b4,#eceae4 50%,#9aa7b2)" role="img" aria-label="Photo of a hospital room with a bed"></div>
<div class="abs tile tile-label" style="left:250px;top:2302px;background:linear-gradient(180deg,#1f3d7a,#3c6aa8)" role="img" aria-label="Photo of a domed government building at dusk">Government<br>Buildings</div>
<div class="abs tile" style="left:411px;top:2302px;background:linear-gradient(160deg,#e9e4dc,#b88a5c 70%,#7d5a3c)" role="img" aria-label="Photo of a classroom with wooden chairs"></div>
<div class="abs tile" style="left:89px;top:2452px;background:linear-gradient(160deg,#e6e9ed,#a9b0ba 60%,#7b4a4a)" role="img" aria-label="Photo of a car service garage"></div>
<div class="abs tile" style="left:250px;top:2452px;background:linear-gradient(160deg,#2f4a3d,#dfe6e3 60%,#9aa7a0)" role="img" aria-label="Photo of a large factory hall"></div>
<div class="abs tile" style="left:411px;top:2452px;background:linear-gradient(160deg,#d8e4ef,#5a7f9c 60%,#7aa05a)" role="img" aria-label="Photo of a glass office lobby with plants"></div>
<div class="abs tile" style="left:572px;top:2452px;background:linear-gradient(160deg,#f0f0f0,#8c8c8c 55%,#3a3a3a)" role="img" aria-label="Photo of gym machines"></div>
<p class="abs svc-copy">Lorem ipsum dolor sit amet, consectetur adipiscing elit, sed do eiusmod tempor incididunt ut labore et dolore magna aliqua. Ut enim ad minim veniam, quis nostrud exercitation ullamco laboriatur.</p>
<a class="abs btn-line" href="#" style="left:957px;top:2464px;width:152px">Read More</a>

<!-- blog -->
<div class="abs blog"></div>
<svg class="abs" style="left:0;top:2680px" width="1200" height="50" viewBox="0 0 1200 50"><path d="M0 0H1200V22C1040 8 880 36 700 30 520 24 380 4 220 10 120 14 60 30 0 40z" fill="#fff"/></svg>
<div class="abs bubble" style="left:96px;top:2774px;width:14px;height:14px"></div>
<div class="abs bubble" style="left:116px;top:2806px;width:9px;height:9px"></div>
<div class="abs bubble" style="left:54px;top:2816px;width:14px;height:14px"></div>
<div class="abs bubble" style="left:82px;top:2836px;width:28px;height:28px"></div>
<div class="abs bubble" style="left:-14px;top:2836px;width:52px;height:52px"></div>
<div class="abs blog-head"><div class="eyebrow" style="margin-bottom:8px">BLOG</div><h2 class="h2">Latest News</h2></div>

<div class="abs card" style="left:89px;top:2902px">
  <div class="img" style="background:radial-gradient(circle at 40% 70%,#c46a2e,#2a2f55 45%,#141a36)" role="img" aria-label="Photo of blurred city lights at night"></div>
  <span class="date">April 22, 2019</span><h4>Featured Content</h4>
  <p>Lorem ipsum dolor sit amet, consectetur adipiscing elit, sed do eiusmod tempor incididunt ut labore</p>
  <div class="foot"><span>Read More</span><svg width="28" height="10" viewBox="0 0 28 10"><path d="M0 5h26M21 1l5 4-5 4" stroke="#1d8fd0" stroke-width="1.6" fill="none"/></svg></div>
</div>
<div class="abs card" style="left:441px;top:2902px">
  <div class="img" style="background:linear-gradient(180deg,#b9a9a4,#8a7a76 45%,#4a3f42)" role="img" aria-label="Photo of a city skyline from above"></div>
  <span class="date">April 22, 2019</span><h4>Featured Content</h4>
  <p>Lorem ipsum dolor sit amet, consectetur adipiscing elit, sed do eiusmod tempor incididunt ut labore</p>
  <div class="foot"><span>Read More</span><svg width="28" height="10" viewBox="0 0 28 10"><path d="M0 5h26M21 1l5 4-5 4" stroke="#1d8fd0" stroke-width="1.6" fill="none"/></svg></div>
</div>
<div class="abs card" style="left:790px;top:2902px">
  <div class="img" style="background:linear-gradient(160deg,#7a5233,#b58a62 50%,#e5e2dc)" role="img" aria-label="Photo of a laptop, notebook and coffee cup on a wooden desk"></div>
  <span class="date">April 22, 2019</span><h4>Featured Content</h4>
  <p>Lorem ipsum dolor sit amet, consectetur adipiscing elit, sed do eiusmod tempor incididunt ut labore</p>
  <div class="foot"><span>Read More</span><svg width="28" height="10" viewBox="0 0 28 10"><path d="M0 5h26M21 1l5 4-5 4" stroke="#1d8fd0" stroke-width="1.6" fill="none"/></svg></div>
</div>

<!-- testimonial -->
<div class="abs testi-photo" role="img" aria-label="Photo of a cleaner in a blue apron spraying and wiping a desk beside a monitor"></div>
<div class="abs testi-card">
  <svg class="abs" style="left:42px;top:-6px" width="40" height="34" viewBox="0 0 40 34"><path d="M16 4C8 6 4 12 4 20a7 7 0 1012-5M36 4c-8 2-12 8-12 16a7 7 0 1012-5" fill="none" stroke="#fbee3f" stroke-width="3"/></svg>
  <div class="name">-Nora Ellis</div>
  <div class="stars">
    <svg width="13" height="13" viewBox="0 0 20 20"><path d="M10 1l2.8 6 6.2.6-4.7 4.2 1.4 6.2L10 14.8 4.3 18l1.4-6.2L1 7.6 7.2 7z" fill="#fff"/></svg>
    <svg width="13" height="13" viewBox="0 0 20 20"><path d="M10 1l2.8 6 6.2.6-4.7 4.2 1.4 6.2L10 14.8 4.3 18l1.4-6.2L1 7.6 7.2 7z" fill="#fff"/></svg>
    <svg width="13" height="13" viewBox="0 0 20 20"><path d="M10 1l2.8 6 6.2.6-4.7 4.2 1.4 6.2L10 14.8 4.3 18l1.4-6.2L1 7.6 7.2 7z" fill="#fff"/></svg>
    <svg width="13" height="13" viewBox="0 0 20 20"><path d="M10 1l2.8 6 6.2.6-4.7 4.2 1.4 6.2L10 14.8 4.3 18l1.4-6.2L1 7.6 7.2 7z" fill="#fff"/></svg>
    <svg width="13" height="13" viewBox="0 0 20 20"><path d="M10 1l2.8 6 6.2.6-4.7 4.2 1.4 6.2L10 14.8 4.3 18l1.4-6.2L1 7.6 7.2 7z" fill="#fff"/></svg>
  </div>
  <p>Lorem ipsum dolor sit amet, consectetur scing elit, sed do eiusmod tempor incididunt ut labore et dolore magna aliqua. Ut enim ad minim veniam, quis nostrud</p>
  <a href="#">Read More</a>
</div>
<div class="abs bubble" style="left:686px;top:3930px;width:50px;height:50px"></div>
<div class="abs bubble" style="left:780px;top:3920px;width:28px;height:28px"></div>
<div class="abs bubble" style="left:756px;top:3900px;width:12px;height:12px"></div>
<div class="abs bubble" style="left:770px;top:3982px;width:52px;height:52px"></div>
<svg class="abs" style="left:0;top:3940px" width="1200" height="80" viewBox="0 0 1200 80"><path d="M0 30C140 60 300 76 460 70 620 64 740 40 880 40 1000 40 1100 20 1200 10V80H0z" fill="#0a0a0a"/></svg>

<!-- footer -->
<footer class="abs footer">
  <div class="abs fcol" style="left:93px;top:78px">
    <h5>Newsletter</h5>
    <p>Get More Informations</p>
    <div class="sub"><span>Email Address</span><b>SUBSCRIBE</b></div>
    <div class="social"><i></i><i></i><i></i><i></i><i></i></div>
  </div>
  <div class="abs fcol" style="left:465px;top:78px">
    <h5>Importants</h5>
    <ul><li>Home</li><li>Services</li><li>News</li><li>Gift Card</li><li>About Us</li><li>Contact</li><li>References</li></ul>
  </div>
  <div class="abs fcol" style="left:638px;top:78px">
    <h5>Other</h5>
    <ul><li>Privacy Policy</li><li>Faq</li><li>Terms &amp; Conditions</li></ul>
  </div>
  <div class="abs fcol" style="left:853px;top:78px;width:260px">
    <h5>Contact Us</h5>
    <p>2214 Shoreline Ave, Bayport,<br>CA 90410<br>+1 555 014 2280<br>hello@tidewellhome.example</p>
    <p style="margin-top:30px">Mon - Thur: 8:00 am - 5:00 pm<br>Sat - Sun: 12:00 pm - 3:00 pm</p>
  </div>
</footer>
<div class="abs copy-bar"><span class="nm">Tidewell Homecare</span><span class="cr">© 2020 Copyrights.The Company Name.All Rights Reserved</span></div>

</body>
</html>
```